Copper Lantern

Need a business card for our restaurant. Restaurant and Bar in the mountains of North Idaho. Rustic looking card

rustic design, wood and metal looking, primarily neutral colors

• Name, address, phone number, website, email address

```html
<!DOCTYPE html>
<html lang="en">
<head>
<meta charset="utf-8">
<title>Copper Lantern – Business Card</title>
<link rel="stylesheet" href="https://fonts.googleapis.com/css2?family=Cinzel:wght@400&family=Montserrat:wght@400;700&display=swap">
<style>
  :root {
    --stage: #202020;
    --card: #1b1b1b;
    --ink: #f2f2f2;
    --ink-soft: #d6d6d6;
    --rule: #bdbdbd;
  }
  * { box-sizing: border-box; margin: 0; padding: 0; }
  html, body { width: 1200px; height: 875px; overflow: hidden; }
  body {
    background: var(--stage);
    font-family: "Montserrat", sans-serif;
    color: var(--ink);
    display: flex;
    align-items: center;
    justify-content: center;
    gap: 60px;
  }
  .card {
    position: relative;
    width: 520px;
    height: 297px;
    background: var(--card);
    border-radius: 16px;
    box-shadow: 0 14px 40px rgba(0,0,0,.45);
  }
  .brand {
    position: absolute;
    display: flex;
    align-items: center;
    justify-content: center;
    border: 4px solid var(--ink);
    border-radius: 50%;
  }
  .brand-name {
    font-family: "Cinzel", serif;
    font-weight: 400;
    color: var(--ink);
    text-align: center;
    letter-spacing: .08em;
    line-height: 1.2;
  }
  .card-front .brand {
    width: 178px; height: 178px;
    left: 171px; top: 60px;
  }
  .card-front .brand-name { font-size: 22px; }
  .card-back .brand {
    width: 118px; height: 118px;
    left: 132px; top: 26px;
    border-width: 3px;
  }
  .card-back .brand-name { font-size: 14px; }
  .person {
    position: absolute;
    right: 290px; top: 178px;
    text-align: right;
  }
  .person-name { font-weight: 700; font-size: 19px; }
  .person-role { font-size: 11px; color: var(--ink-soft); margin-top: 2px; }
  .divider {
    position: absolute;
    left: 244px; top: 148px;
    width: 1px; height: 80px;
    background: var(--rule);
  }
  .contacts {
    position: absolute;
    left: 256px; top: 146px;
    list-style: none;
    font-size: 11.5px;
  }
  .contacts li {
    display: flex; align-items: center; gap: 8px;
    height: 21px;
  }
  .contacts svg { width: 11px; height: 11px; fill: var(--ink); flex: none; }
  .address {
    position: absolute;
    left: 0; width: 100%;
    top: 252px;
    text-align: center;
    font-size: 11.5px;
    padding-left: 40px;
  }
</style>
</head>
<body>
  <section class="card card-front" aria-label="Card front">
    <div class="brand"><span class="brand-name">Copper<br>Lantern</span></div>
  </section>

  <section class="card card-back" aria-label="Card back">
    <div class="brand"><span class="brand-name">Copper<br>Lantern</span></div>

    <div class="person">
      <p class="person-name">Mara Ellison</p>
      <p class="person-role">Managing Director</p>
    </div>

    <div class="divider"></div>

    <ul class="contacts">
      <li>
        <svg viewBox="0 0 16 16" aria-hidden="true"><path d="M3 1h3l1.5 4-2 1.3a9 9 0 0 0 4.2 4.2L11 8.5l4 1.5v3a2 2 0 0 1-2 2A13 13 0 0 1 1 3a2 2 0 0 1 2-2z"/></svg>
        (208) 555 0147
      </li>
      <li>
        <svg viewBox="0 0 16 16" aria-hidden="true"><path d="M1 3h14v10H1z M1.5 3.5 8 9l6.5-5.5" stroke="#1b1b1b" stroke-width="1.2"/></svg>
        hello@copperlantern.com
      </li>
      <li>
        <svg viewBox="0 0 16 16" aria-hidden="true"><circle cx="8" cy="8" r="7"/><path d="M1 8h14M8 1c-3 3.5-3 10.5 0 14M8 1c3 3.5 3 10.5 0 14" stroke="#1b1b1b" stroke-width="1" fill="none"/></svg>
        www.copperlantern.com
      </li>
    </ul>

    <p class="address">48 Ridge Road, Pine Hollow, USA</p>
  </section>
</body>
</html>
```